Business Card Design for Training Business

Clear Path Coaching is a new business that delivers training and other services with a focus on topics related to mental health and wellbeing, for example, Wellmind Response Course, Resilience etc. We have a strong focus on evidence-based psychology and neuroscience. I have a logo which I will upload with the brief, so please consider colours that work well with the logo.
Target Market(s)
Adults, workplaces (particularly government and not-for-profits)
Industry/Entity Type
Business
Contact Information for Business Card
Head Strong TrainingSamantha SellwoodDirector0438 770 850sam@headstrongtraining.com.auwww.headstrongtraining.com.au

```html
<!DOCTYPE html>
<html lang="en">
<head>
<meta charset="utf-8">
<title>Clear Path Coaching – Business Card</title>
<link rel="stylesheet" href="https://fonts.googleapis.com/css2?family=Arimo:wght@400;700&display=swap">
<style>
  :root {
    --backdrop: #4a403b;
    --card: #1c1c1d;
    --card-edge: #111112;
    --brand-grey: #9a9ca0;
    --text-light: #e6e6e6;
    --accent: #2bb8b9;
    --divider: #9a9a9a;
  }
  * { box-sizing: border-box; margin: 0; padding: 0; }
  html, body { width: 1200px; height: 787px; overflow: hidden; }
  body {
    background: var(--backdrop);
    font-family: "Arimo", Arial, sans-serif;
    display: flex;
    align-items: center;
    justify-content: center;
    gap: 40px;
  }
  .card {
    position: relative;
    width: 540px;
    height: 330px;
    background: var(--card);
    border: 1px solid var(--card-edge);
    box-shadow: 0 10px 30px rgba(0, 0, 0, 0.45);
  }

  /* business name placeholder: one colour, one weight, plain */
  .brand-name {
    color: var(--brand-grey);
    font-weight: 400;
    line-height: 1.2;
    text-align: center;
    white-space: nowrap;
  }

  /* back side */
  .card-back .brand-name {
    position: absolute;
    left: 0; right: 0;
    top: 130px;
    font-size: 26px;
  }
  .card-back .website {
    position: absolute;
    left: 0; right: 0;
    bottom: 64px;
    text-align: center;
    color: var(--text-light);
    font-size: 15px;
    letter-spacing: 0.3px;
  }

  /* front side */
  .card-front .brand-name {
    position: absolute;
    left: 10px;
    width: 242px;
    top: 150px;
    font-size: 21px;
  }
  .divider {
    position: absolute;
    left: 262px;
    top: 60px;
    width: 1px;
    height: 210px;
    background: linear-gradient(to bottom, transparent, var(--divider) 30%, var(--divider) 70%, transparent);
  }
  .contact { position: absolute; left: 284px; top: 96px; right: 12px; color: var(--text-light); }
  .person-name { color: var(--accent); font-size: 20px; font-weight: 700; }
  .person-role { font-size: 13px; margin-top: 4px; }
  .contact-list { list-style: none; margin-top: 22px; }
  .contact-list li {
    display: flex;
    align-items: center;
    gap: 10px;
    font-size: 13px;
    margin-bottom: 9px;
    white-space: nowrap;
  }
  .contact-icon { width: 14px; height: 14px; flex: none; fill: var(--accent); }
</style>
</head>
<body>
  <section class="card card-back" aria-label="Card back">
    <p class="brand-name">Clear Path Coaching</p>
    <p class="website">www.clearpathcoaching.example.au</p>
  </section>

  <section class="card card-front" aria-label="Card front">
    <p class="brand-name">Clear Path Coaching</p>
    <span class="divider"></span>
    <div class="contact">
      <p class="person-name">Rebecca Tanfield</p>
      <p class="person-role">Director</p>
      <ul class="contact-list">
        <li>
          <svg class="contact-icon" viewBox="0 0 24 24" aria-hidden="true"><path d="M6.6 10.8a15.1 15.1 0 0 0 6.6 6.6l2.2-2.2a1 1 0 0 1 1-.25 11.4 11.4 0 0 0 3.6.57 1 1 0 0 1 1 1V20a1 1 0 0 1-1 1A17 17 0 0 1 3 4a1 1 0 0 1 1-1h3.5a1 1 0 0 1 1 1c0 1.25.2 2.45.57 3.57a1 1 0 0 1-.25 1z"/></svg>
          0491 362 517
        </li>
        <li>
          <svg class="contact-icon" viewBox="0 0 24 24" aria-hidden="true"><path d="M2 5h20v14H2z"/><path d="M3 6l9 7 9-7" fill="none" stroke="var(--card)" stroke-width="1.6"/></svg>
          bec@clearpathcoaching.example.au
        </li>
        <li>
          <svg class="contact-icon" viewBox="0 0 24 24" aria-hidden="true"><circle cx="12" cy="12" r="10"/><path d="M2 12h20M12 2c3 3 3 17 0 20M12 2c-3 3-3 17 0 20" fill="none" stroke="var(--card)" stroke-width="1.5"/></svg>
          www.clearpathcoaching.example.au
        </li>
      </ul>
    </div>
  </section>
</body>
</html>
```